Verlindo Magician

I want the business card for my business to give to people who watch that later I will be employed to show magic here is my website http://www.balsamomagicien.com/I want the interesting design , i am very opened for formal and informal, I watch a lot of design so don't stick to the common shape and form but i hope it can also be produced the thing to write on will be the same as in picture that i will upload , i also will upload the logo for you that so can be easy to useDenis CostilleMagicianMAGICIAN VERLINDO 17 rue des Tilleuls - 25000 BESANÇON contact@verlindoillusions.example tel. 0381 946 157 tel. 0674 219 503

```html
<!DOCTYPE html>
<html lang="fr">
<head>
<meta charset="utf-8">
<title>Verlindo Magician – Business Card</title>
<link href="https://fonts.googleapis.com/css2?family=Raleway:wght@300;400;500;600&display=swap" rel="stylesheet">
<style>
  :root {
    --backdrop: #b8a486;
    --card-dark: #262626;
    --card-light: #ffffff;
    --ink-light: #f2f2f2;
    --ink-dark: #1a1a1a;
    --accent: #e32b2f;
    --rule: #6a6a6a;
    --art-dark: #111111;
    --art-mid: #3a3a3a;
    --pattern-grey: #ecebeb;
    --pattern-pink: #f7e9e9;
  }
  * { box-sizing: border-box; margin: 0; padding: 0; }
  html, body { width: 1200px; height: 768px; overflow: hidden; }
  body {
    background: var(--backdrop);
    font-family: "Raleway", sans-serif;
    position: relative;
  }
  .card {
    position: absolute;
    border-radius: 18px;
    overflow: hidden;
    box-shadow: 0 10px 30px rgba(0,0,0,.25);
  }
  /* Front */
  .card-front {
    left: 70px; top: 224px;
    width: 560px; height: 320px;
    background: var(--card-dark);
    color: var(--ink-light);
  }
  .portrait-front {
    position: absolute;
    left: 22px; bottom: 0;
    width: 238px; height: 220px;
    border-radius: 100px 100px 0 0;
    background: linear-gradient(160deg, var(--art-mid), var(--art-dark));
    border: 2px solid #dcdcdc;
    border-bottom: none;
  }
  .front-info {
    position: absolute;
    right: 22px; top: 42px;
    width: 256px;
    text-align: center;
  }
  .holder-name {
    color: var(--accent);
    font-size: 25px;
    font-weight: 500;
    letter-spacing: .5px;
    text-transform: uppercase;
    white-space: nowrap;
  }
  .holder-role {
    font-size: 11px;
    letter-spacing: 1px;
    margin-top: 4px;
    text-transform: uppercase;
  }
  .suit-red { color: var(--accent); }
  .dots { display: flex; justify-content: center; gap: 3px; margin-top: 14px; }
  .dot { width: 13px; height: 13px; border-radius: 50%; background: var(--accent); }
  .divider { width: 120px; height: 1px; background: var(--rule); margin: 14px auto; }
  .contact-lines { font-size: 11.5px; line-height: 1.55; font-weight: 400; white-space: nowrap; }
  .contact-lines .gap { height: 8px; }

  /* Back */
  .card-back {
    left: 780px; top: 104px;
    width: 320px; height: 560px;
    background: var(--card-light);
    color: var(--ink-dark);
  }
  .back-pattern {
    position: absolute; inset: 0;
    background:
      radial-gradient(ellipse at 30% 25%, var(--pattern-pink), transparent 60%),
      radial-gradient(ellipse at 75% 80%, var(--pattern-pink), transparent 55%),
      linear-gradient(180deg, var(--pattern-grey), #faf8f8);
  }
  .portrait-back {
    position: absolute;
    left: 55px; top: 150px;
    width: 210px; height: 170px;
    border-radius: 90px 90px 20px 20px;
    background: linear-gradient(160deg, var(--art-mid), var(--art-dark));
  }
  .brand {
    position: absolute;
    left: 0; right: 0; top: 336px;
    text-align: center;
  }
  .brand-name {
    font-size: 40px;
    font-weight: 300;
    letter-spacing: 3px;
  }
  .brand-sub {
    font-size: 10px;
    letter-spacing: 1.5px;
    margin-top: 2px;
    padding-left: 90px;
    text-transform: uppercase;
  }
</style>
</head>
<body>

  <section class="card card-front">
    <div class="portrait-front" role="img" aria-label="Black and white illustration of the magician holding a playing card"></div>
    <div class="front-info">
      <h1 class="holder-name">Marc Ravoulet</h1>
      <p class="holder-role">♠<span class="suit-red">♦</span> Magicien <span class="suit-red">♥</span>♣</p>
      <div class="dots"><span class="dot"></span><span class="dot"></span><span class="dot"></span><span class="dot"></span></div>
      <div class="divider"></div>
      <div class="contact-lines">
        <p>MAGICIAN VERLINDO</p>
        <p>17 rue des Tilleuls - 25000 BESANÇON</p>
        <div class="gap"></div>
        <p>0381 946 157 | 0674 219 503</p>
        <p>contact@verlindoillusions.example</p>
        <p>www.verlindoillusions.example</p>
      </div>
    </div>
  </section>

  <section class="card card-back">
    <div class="back-pattern" role="img" aria-label="Faint repeating pattern of card suits in light grey and pink"></div>
    <div class="portrait-back" role="img" aria-label="Black and white illustration of the magician holding a playing card"></div>
    <div class="brand">
      <p class="brand-name">VERLINDO</p>
      <p class="brand-sub">♠<span class="suit-red">♦</span> Magicien <span class="suit-red">♥</span>♣</p>
    </div>
  </section>

</body>
</html>
```